Corporate Travel Technology Company needs new Business Card design

We need a new business card design to reflect our re-branded company. Our company is called tolvEn (pronounced tolvenn) and we provide Business Intelligence and mobile travel management solutions for the corporate travel industry. Our multinational customers use our solutions to manage large travel budgets and frequent travellers, as well as to save money and reduce risk. We'd like to see designs that use the blue and green palette as well as our corporate logo (attached below). The design should communicate innovation, insight, forward thinking, contemporary, trusted.

Target Market(s)

Large multinational corporates and Travel Agencies.

Industry/Entity Type

Business

Contact Information for Business Card

Rosalind Mercer
Chief Executive
tolvEn
Phone number - +61 (0)2 8134 2907
Email address - rosalind.mercer@tolven-example.com
Mobile number - +61 (0)438 516 702
www.tolven-example.com

Font styles to use
Other font styles liked:
• Please use font as close to corporate logo as possible

Colors
0255a3
0393ce
00a990
33b8a4
33a6d7
3176b5

Requirements
Must have
• Please include the words;
• Mobile Travel Management
• Accelerating Travel Business Insights
• Use corporate logo - although icon can be stylised if needed

```html
<!DOCTYPE html>
<html lang="en">
<head>
<meta charset="utf-8">
<title>tolvEn Business Card</title>
<link rel="stylesheet" href="https://fonts.googleapis.com/css2?family=Montserrat:wght@300;400;600;700&display=swap">
<style>
  :root {
    --page-bg: #e9ecee;
    --slate-light: #56676a;
    --slate-dark: #263133;
    --brand-blue: #33a6d7;
    --brand-sky: #4fc3ee;
    --brand-deep: #0a7fcf;
    --ink-grey: #4a5456;
    --white: #ffffff;
    --muted-white: #dfe6e8;
  }
  * { box-sizing: border-box; margin: 0; padding: 0; }
  html, body {
    width: 1200px; height: 913px; overflow: hidden;
    background: var(--page-bg);
    font-family: "Montserrat", Arial, sans-serif;
  }
  .canvas {
    width: 1200px; height: 913px;
    display: flex; align-items: center; justify-content: center; gap: 40px;
  }
  .card {
    position: relative;
    width: 540px; height: 309px;
    border-radius: 4px;
    overflow: hidden;
    box-shadow: 0 10px 28px rgba(0,0,0,0.18);
  }

  /* Front: contact side */
  .card-front {
    background: linear-gradient(160deg, var(--slate-light) 0%, #3c4a4d 45%, var(--slate-dark) 100%);
  }
  .swoosh { position: absolute; inset: 0; width: 100%; height: 100%; }
  .front-wordmark {
    position: absolute; left: 34px; top: 128px;
    display: flex; align-items: center; gap: 12px;
  }
  .wordmark-dot {
    width: 30px; height: 30px; border-radius: 50%;
    border: 3px solid var(--white);
  }
  .wordmark-text {
    font-weight: 400; font-size: 56px; letter-spacing: 1px;
    color: var(--brand-blue); line-height: 1;
  }
  .holder {
    position: absolute; right: 28px; top: 22px; text-align: right;
  }
  .holder-name {
    font-weight: 700; font-size: 17px; letter-spacing: 1px;
    color: var(--brand-blue); text-transform: uppercase;
  }
  .holder-title {
    font-weight: 300; font-size: 12px; color: var(--muted-white); margin-top: 3px;
  }
  .contact-list {
    position: absolute; right: 28px; top: 140px;
    list-style: none; text-align: right;
  }
  .contact-item {
    display: flex; align-items: center; justify-content: flex-end; gap: 8px;
    font-weight: 300; font-size: 10.5px; color: var(--brand-blue);
    line-height: 17px;
  }
  .contact-icon { width: 10px; height: 10px; flex: none; }

  /* Back: brand side */
  .card-back {
    background: linear-gradient(165deg, var(--brand-sky) 0%, #2fa9e3 50%, var(--brand-deep) 100%);
  }
  .back-glow {
    position: absolute; width: 420px; height: 420px; border-radius: 50%;
    background: rgba(255,255,255,0.07);
  }
  .back-glow.one { left: -140px; top: 70px; }
  .back-glow.two { right: -160px; top: -200px; }
  .back-brand {
    position: absolute; inset: 0;
    display: flex; flex-direction: column; align-items: center; justify-content: center;
  }
  .back-wordmark {
    display: flex; align-items: center; gap: 12px;
  }
  .back-wordmark .wordmark-text { color: var(--ink-grey); font-size: 62px; }
  .taglines { margin-top: 18px; text-align: center; }
  .tagline {
    font-weight: 600; font-size: 12.5px; color: var(--white); line-height: 18px;
    letter-spacing: 0.3px;
  }
</style>
</head>
<body>
<main class="canvas">
  <section class="card card-front" aria-label="Business card front">
    <svg class="swoosh" viewBox="0 0 540 309" aria-hidden="true">
      <path d="M150 309 C215 255, 235 185, 295 130 C355 85, 445 80, 540 78 L540 86 C450 88, 365 100, 305 142 C248 195, 228 262, 166 309 Z" fill="#ffffff"/>
    </svg>
    <div class="front-wordmark">
      <span class="wordmark-dot"></span>
      <span class="wordmark-text">tolvEn</span>
    </div>
    <div class="holder">
      <p class="holder-name">Rosalind Mercer</p>
      <p class="holder-title">Chief Executive</p>
    </div>
    <ul class="contact-list">
      <li class="contact-item">+61 (0)438 516 702
        <svg class="contact-icon" viewBox="0 0 10 10" aria-hidden="true"><rect x="2.5" y="0.5" width="5" height="9" rx="1" fill="none" stroke="#fff"/><line x1="4" y1="8" x2="6" y2="8" stroke="#fff"/></svg>
      </li>
      <li class="contact-item">+61 (0)2 8134 2907
        <svg class="contact-icon" viewBox="0 0 10 10" aria-hidden="true"><path d="M2 1 L4 1 L4.6 3.2 L3.4 4.2 C4 5.6 4.6 6.2 5.8 6.7 L6.8 5.5 L9 6.1 L9 8 C9 8.6 8.6 9 8 9 C4.5 9 1 5.5 1 2 C1 1.4 1.4 1 2 1 Z" fill="#fff"/></svg>
      </li>
      <li class="contact-item">www.tolven-example.com
        <svg class="contact-icon" viewBox="0 0 10 10" aria-hidden="true"><circle cx="5" cy="5" r="4.3" fill="none" stroke="#fff"/><ellipse cx="5" cy="5" rx="1.8" ry="4.3" fill="none" stroke="#fff" stroke-width="0.8"/><line x1="0.7" y1="5" x2="9.3" y2="5" stroke="#fff" stroke-width="0.8"/></svg>
      </li>
      <li class="contact-item">rosalind.mercer@tolven-example.com
        <svg class="contact-icon" viewBox="0 0 10 10" aria-hidden="true"><rect x="0.5" y="2" width="9" height="6" fill="none" stroke="#fff"/><polyline points="0.5,2 5,5.5 9.5,2" fill="none" stroke="#fff"/></svg>
      </li>
    </ul>
  </section>

  <section class="card card-back" aria-label="Business card back">
    <span class="back-glow one"></span>
    <span class="back-glow two"></span>
    <div class="back-brand">
      <div class="back-wordmark">
        <span class="wordmark-dot"></span>
        <span class="wordmark-text">tolvEn</span>
      </div>
      <div class="taglines">
        <p class="tagline">Mobile Travel Management</p>
        <p class="tagline">Accelerating Travel Business Insights</p>
      </div>
    </div>
  </section>
</main>
</body>
</html>
```